Event Website for the Audio & Visual Industry

Convene is an exhibition aimed at meeting the business needs of audio and visual professionals – the visitors are the ones that make purchase decisions when buying anything to do with AV installation, Lighting & Entertainment Technology, DJ Technologies and even Musical Instruments.

We need to rebuild our website to reflect the professional look but with a bit of creativity/flare that is associated with the industry.

Websites whose design is along the lines we're looking for:

• http:www.pelmora.com.au
• http:www.kavrin.com
• http://www.brightpanelfair.net/ (competitor expo, like the layout. Not fantastic though, but the best I’ve seen from the industry)
• http://www.tuvelo.com.au and http://www.ostrand.com.au/ (Like these brand websites, they are clean and corporate but the use of imagery allows it to have some personality)

Target Market(s)

Corporate AV End Users, Lighting Designers, Concert/Entertainment companies, Sound Engineers

Industry/Entity Type

Business

Requirements
Must have
• Refer to the current splash page – www.convene-expo.com
This is the look and feel we have developed for our brochure. We want to expand on this and create a professional corporate look and feel without alienating existing sound, light and vision sectors.

The website's focus is to register visitors to attend the show. Please include a floating 'Register Free' Call to action. Please also include floating social media buttons. For what I mean by 'floating' check out the Social media buttons on this website: http://quorvix.com/2012/02/19/tall-boat-preview/ (scroll down to see effect).

We'll like to include a Rotating Banner at the top.

Sponsor element at the bottom off the page.

Sign up form functionality

Menu to be: About the Show, What's On, Register, How to Exhibit, Blog, Contact us.

I would like to see designs for a content page as well as the homepage.

```html
<!DOCTYPE html>
<html lang="en">
<head>
<meta charset="utf-8">
<title>Convene 2012</title>
<link rel="stylesheet" href="https://fonts.googleapis.com/css2?family=Gelasio&family=Open+Sans:wght@400;600&family=Roboto+Condensed:wght@700&family=Arimo:wght@400;700&display=swap">
<style>
  :root {
    --page-bg: #f8f8f8;
    --white: #ffffff;
    --ink: #111111;
    --band: #000000;
    --brand-red: #d0021b;
    --muted: #555555;
    --rule: #d8d8d8;
    --tab-text: #9a9a9a;
  }
  * { margin: 0; padding: 0; box-sizing: border-box; }
  html, body { width: 1200px; height: 966px; overflow: hidden; }
  body {
    position: relative;
    background: linear-gradient(to bottom, var(--white) 0, var(--white) 557px, var(--page-bg) 557px);
    font-family: "Open Sans", Arial, sans-serif;
    color: var(--ink);
  }
  .site {
    position: absolute; left: 67px; top: 0; width: 1066px; height: 956px;
    background: var(--white);
    box-shadow: 1px 0 0 #c8c8c8, 2px 2px 3px rgba(0,0,0,.08);
  }
  .hero-banner {
    position: absolute; left: 0; top: 49px; width: 1066px; height: 511px;
    background:
      linear-gradient(to right, rgba(0,0,0,.55) 0, rgba(0,0,0,0) 12%),
      linear-gradient(to bottom, #3c4a66 0%, #8a7f96 22%, #c9a07a 45%, #e9b45a 62%, #9a5a1c 80%, #2a1a0c 100%);
  }
  .header-panel { position: absolute; left: 0; top: 49px; width: 1066px; height: 80px; }
  .logo { position: absolute; left: 80px; top: 54px; display: flex; align-items: center; }
  .logo-dot { width: 12px; height: 12px; border-radius: 50%; background: var(--brand-red); margin-right: 9px; }
  .logo-name { font-family: "Open Sans", Arial, sans-serif; font-weight: 600; font-size: 30px; line-height: 1; color: var(--ink); }
  .signup { position: absolute; left: 707px; top: 25px; display: flex; align-items: center; }
  .signup-label { font-family: "Arimo", Arial, sans-serif; font-weight: 700; font-size: 12px; color: var(--brand-red); }
  .signup-field {
    width: 165px; height: 22px; margin-left: 9px; background: var(--white);
    border: none; border-bottom: 1px solid var(--rule); border-right: 1px solid var(--rule);
  }
  .signup-go { margin-left: 10px; }
  .main-nav { position: absolute; top: 86px; left: 0; font-size: 12.5px; }
  .main-nav a { position: absolute; color: var(--ink); text-decoration: none; white-space: nowrap; }
  .info-band {
    position: absolute; left: 0; top: 560px; width: 1066px; height: 128px; background: var(--band); color: var(--white);
  }
  .highlights {
    position: absolute; left: 57px; top: 13px; list-style: none;
    font-family: "Roboto Condensed", "Arial Narrow", sans-serif; font-weight: 700; font-size: 18.5px; line-height: 22.6px;
  }
  .event-details { position: absolute; left: 350px; top: 17px; font-family: "Gelasio", Georgia, serif; font-size: 18px; line-height: 22.5px; letter-spacing: .3px; }
  .event-details .calendar { position: absolute; left: -29px; top: 1px; }
  .event-details p { text-transform: uppercase; white-space: nowrap; }
  .flyer { position: absolute; left: 789px; top: 66px; display: flex; align-items: center; color: var(--white); text-decoration: none; font-family: "Roboto Condensed", Arial, sans-serif; font-weight: 700; font-size: 13px; }
  .flyer svg { margin-right: 14px; }
  .intro {
    position: absolute; left: 22px; top: 717px; width: 1010px;
    font-family: "Gelasio", Georgia, serif; font-size: 18.6px; line-height: 22.4px; color: var(--brand-red);
  }
  .site-footer { position: absolute; left: 0; top: 809px; width: 1066px; height: 147px; background: var(--page-bg); border-top: 1px solid #efefef; }
  .legal { position: absolute; left: 26px; top: 42px; font-family: "Arimo", Arial, sans-serif; font-size: 9.2px; line-height: 13px; color: #333; }
  .organiser { position: absolute; left: 760px; top: 56px; display: flex; align-items: center; }
  .organiser-square { width: 10px; height: 10px; background: var(--brand-red); margin-right: 7px; }
  .organiser-name { font-family: "Arimo", Arial, sans-serif; font-weight: 700; font-size: 15px; color: var(--ink); }
  .side-tab {
    position: absolute; left: -6px; top: 667px; width: 29px; height: 182px;
    background: var(--white); border: 1px solid var(--rule); border-radius: 0 10px 10px 0;
  }
  .side-tab span {
    position: absolute; left: 6px; top: 56px; writing-mode: vertical-rl;
    font-family: "Arimo", Arial, sans-serif; font-weight: 700; font-size: 10px; color: var(--tab-text); white-space: nowrap;
  }
</style>
</head>
<body>
  <div class="site">
    <div class="hero-banner" role="img" aria-label="Rotating banner photo: harbour opera house and arch bridge lit gold at dusk"></div>

    <svg class="header-panel" viewBox="0 0 1066 80" aria-hidden="true">
      <polygon points="37,0 1032,0 1001,80 77,80" fill="#ffffff" stroke="#e2e2e2"/>
    </svg>

    <header>
      <div class="logo">
        <span class="logo-dot"></span>
        <span class="logo-name">Convene</span>
      </div>

      <form class="signup">
        <span class="signup-label">sign up here</span>
        <input class="signup-field" type="text" aria-label="Email address">
        <svg class="signup-go" width="19" height="19" viewBox="0 0 19 19" aria-label="Submit">
          <circle cx="9.5" cy="9.5" r="8.3" fill="#fff" stroke="#d0021b" stroke-width="1.6"/>
          <polygon points="7.5,5.5 12.5,9.5 7.5,13.5" fill="#d0021b"/>
        </svg>
      </form>

      <nav class="main-nav">
        <a href="#" style="left:359px">About the Show</a>
        <a href="#" style="left:503px">What's On</a>
        <a href="#" style="left:615px">Register</a>
        <a href="#" style="left:714px">How to Exhibit</a>
        <a href="#" style="left:850px">Blog</a>
        <a href="#" style="left:929px">Contact us</a>
      </nav>
    </header>

    <section class="info-band">
      <ul class="highlights">
        <li>NEW LOCATION</li>
        <li>EVEN BIGGER SHOW</li>
        <li>NEW SEMINARS</li>
        <li>EVEN MORE SURPRISES</li>
      </ul>
      <div class="event-details">
        <svg class="calendar" width="20" height="19" viewBox="0 0 20 19" aria-hidden="true">
          <rect x="1" y="3" width="18" height="15" fill="#fff"/>
          <rect x="4" y="0" width="2" height="4" fill="#fff"/><rect x="14" y="0" width="2" height="4" fill="#fff"/>
          <g fill="#000">
            <rect x="3" y="7" width="3" height="2"/><rect x="7" y="7" width="3" height="2"/><rect x="11" y="7" width="3" height="2"/><rect x="15" y="7" width="2" height="2"/>
            <rect x="3" y="10" width="3" height="2"/><rect x="7" y="10" width="3" height="2"/><rect x="11" y="10" width="3" height="2"/><rect x="15" y="10" width="2" height="2"/>
            <rect x="3" y="13" width="3" height="2"/><rect x="7" y="13" width="3" height="2"/><rect x="11" y="13" width="3" height="2"/><rect x="15" y="13" width="2" height="2"/>
          </g>
        </svg>
        <p>21st-23rd August 2012</p>
        <p>Harbourside Convention &amp; Exhibition Centre, Cove Quay</p>
      </div>
      <a class="flyer" href="#">
        <svg width="30" height="36" viewBox="0 0 30 36" aria-hidden="true">
          <polygon points="0,0 22,0 30,8 30,36 0,36" fill="#fff"/>
          <polygon points="22,0 30,8 22,8" fill="#ddd"/>
          <rect x="0" y="28" width="30" height="8" fill="#d0021b"/>
        </svg>
        download the flyer here
      </a>
    </section>

    <p class="intro">With over 500 brands on display, Convene in association with AVLink International, brings together the worlds of ICT, integrating all areas including Visual, Education, Entertainment, Audio &amp; Lighting Technology, Worship, Digital Signage and Unified Communications.</p>

    <footer class="site-footer">
      <p class="legal">
        STRICTLY TRADE ONLY. Entry is restricted to members of the ICT, Audio Visual and Entertainment industries.<br>
        &nbsp;Persons not in these categories, including children will not be admitted at any time.<br>
        &nbsp;© 2011 Halvern Exhibitions, Australia. All rights reserved. Mezzanine level, 118 Marlow Street, Sydney, NSW 2000, Australia.<br>
        &nbsp;Telephone: +61 2 9000 4100. Facsimile: +61 2 9000 4199.
      </p>
      <div class="organiser">
        <span class="organiser-square"></span>
        <span class="organiser-name">Halvern Exhibitions Australia</span>
      </div>
    </footer>
  </div>

  <aside class="side-tab"><span>find us / register</span></aside>
</body>
</html>
```